Business Card Design needed for start up company Halvora

In need of a new business card designed for a start up company based in Sydney, Halvora is a new start up innovative Company, our mission it to make property accessible for everyday Australian and to become the leading Real Estate platform in Australia. We want it to be fresh and clean.

Industry/Entity Type

Financial

Contact Information for Business Card

Section for Name
Section for Title

HALVORA - The Strength of Pooling
Mobile:
Direct:

Font styles to use
Sans Serif

Colors
33a6d7
0692cd
0255a3
ffffff

Requirements
Must have
• Logo, all business card details

```html
<!DOCTYPE html>
<html lang="en">
<head>
<meta charset="utf-8">
<title>Halvora – Business Card</title>
<link href="https://fonts.googleapis.com/css2?family=Open+Sans:wght@400;600;700&display=swap" rel="stylesheet">
<style>
  :root {
    --sky: #33a6d7;
    --ocean: #0692cd;
    --royal: #0255a3;
    --navy: #16397a;
    --white: #ffffff;
    --paper: #f7f8f9;
    --stage: #e6e8eb;
    --soft-white: #dbe6f3;
  }
  * { margin: 0; padding: 0; box-sizing: border-box; }
  html, body {
    width: 1200px; height: 960px; overflow: hidden;
    background: var(--stage);
    font-family: "Open Sans", sans-serif;
  }
  .sheet { position: relative; width: 1200px; height: 960px; }
  .card {
    position: absolute; left: 285px;
    width: 630px; height: 360px;
    overflow: hidden;
    box-shadow: 0 6px 18px rgba(0,0,0,0.18);
  }
  .brand-name {
    position: absolute; left: 0; right: 0;
    text-align: center;
    font-weight: 600; font-size: 54px; line-height: 1;
    letter-spacing: 0.5px;
  }
  /* Back side */
  .card-back {
    top: 90px;
    background: linear-gradient(135deg, var(--sky) 0%, var(--ocean) 100%);
    color: var(--white);
  }
  .card-back .brand-name { top: 136px; color: var(--white); }
  .tagline {
    position: absolute; left: 0; right: 0; top: 262px;
    text-align: center; font-size: 15px; font-weight: 400;
  }
  /* Front side */
  .card-front { top: 510px; background: var(--paper); }
  .card-front .brand-name { top: 70px; color: var(--royal); }
  .band { position: absolute; left: 0; top: 0; width: 630px; height: 360px; }
  .person { position: absolute; left: 40px; top: 236px; }
  .person-name {
    color: var(--sky); font-weight: 700; font-size: 17px; letter-spacing: 0.5px;
  }
  .person-title {
    color: var(--white); font-weight: 400; font-size: 15px; margin-top: 2px;
  }
  .contact {
    position: absolute; left: 380px; top: 216px;
    color: var(--soft-white); font-size: 14px; line-height: 20px;
    list-style: none;
  }
  .contact li { display: flex; align-items: center; gap: 8px; }
  .contact .plain { padding-left: 22px; }
  .contact svg { width: 14px; height: 14px; flex: none; }
</style>
</head>
<body>
<main class="sheet">

  <section class="card card-back" aria-label="Back of business card">
    <p class="brand-name">Halvora</p>
    <p class="tagline">The Strength of Pooling</p>
  </section>

  <section class="card card-front" aria-label="Front of business card">
    <svg class="band" viewBox="0 0 630 360" aria-hidden="true">
      <defs>
        <linearGradient id="bandShade" x1="0" y1="0" x2="0" y2="1">
          <stop offset="0" stop-color="#1d4a8e"/>
          <stop offset="1" stop-color="#14336e"/>
        </linearGradient>
      </defs>
      <path d="M0 200 H150 L160 188 L170 200 H630 V360 H0 Z" fill="url(#bandShade)"/>
      <path d="M0 200 H150 L160 188 L170 200 H630" fill="none" stroke="#33a6d7" stroke-width="3"/>
    </svg>

    <p class="brand-name">Halvora</p>

    <div class="person">
      <p class="person-name">ELENA MARSH</p>
      <p class="person-title">CEO/FOUNDER</p>
    </div>

    <ul class="contact">
      <li class="plain">42 Wattle Grove Road</li>
      <li class="plain">Sydney, NSW 2010</li>
      <li>
        <svg viewBox="0 0 14 14" aria-hidden="true"><path d="M3 1h2l1 3-1.5 1a7 7 0 0 0 4.5 4.5L10 8l3 1v2a2 2 0 0 1-2 2A10 10 0 0 1 1 3a2 2 0 0 1 2-2z" fill="#33a6d7"/></svg>
        02 8123 4567
      </li>
      <li>
        <svg viewBox="0 0 14 14" aria-hidden="true"><rect x="3.5" y="0.5" width="7" height="13" rx="1.5" fill="none" stroke="#33a6d7" stroke-width="1.4"/><circle cx="7" cy="11" r="0.9" fill="#33a6d7"/></svg>
        0412 555 908
      </li>
      <li>
        <svg viewBox="0 0 14 14" aria-hidden="true"><rect x="1" y="3" width="12" height="8" fill="#33a6d7"/><path d="M1 3l6 5 6-5" fill="none" stroke="#16397a" stroke-width="1"/></svg>
        elena@halvora.com
      </li>
      <li>
        <svg viewBox="0 0 14 14" aria-hidden="true"><circle cx="7" cy="7" r="6" fill="#33a6d7"/><path d="M1 7h12M7 1c-2.5 3-2.5 9 0 12M7 1c2.5 3 2.5 9 0 12" fill="none" stroke="#16397a" stroke-width="0.9"/></svg>
        www.halvora.com
      </li>
    </ul>
  </section>

</main>
</body>
</html>
```